International aerospace industry business needs a new brochure

We need to make a new Brochure 4 pages A4:
- like the old one (file Vermondix_test_coupons_thermal_spray.pdf)
- with the new text (tekst_na_ulotke_v9.docx)
- with the new design as in email graphic (20201019_FINAL_Test Coupons v2.psd or .png).

Requirements
Must have
• design as in email graphic (20201019_FINAL_Test Coupons v2.psd or .png)
with the new text (tekst_na_ulotke_v9.docx)
Nice to have
• photos with our employees on production floor may be used.

```html
<!DOCTYPE html>
<html lang="en">
<head>
<meta charset="utf-8">
<title>Vermondix – Test Coupons</title>
<link rel="stylesheet" href="https://fonts.googleapis.com/css2?family=Noto+Sans:wght@400;700&family=Roboto+Condensed:wght@700&display=swap">
<style>
  :root {
    --heading-blue: #2f55a4;
    --text: #1b1b1b;
    --panel-grey: #e4e4e4;
    --banner-grey: #ebebee;
    --frame-blue: #3a5aa8;
    --icon-orange: #e8823a;
    --tip-red: #e8383d;
    --wave-blue: #d9e8f6;
  }
  html, body { margin: 0; padding: 0; }
  body {
    width: 848px; height: 1200px; overflow: hidden; position: relative;
    background: #fff; color: var(--text);
    font-family: "Noto Sans", Verdana, sans-serif; font-size: 15px; letter-spacing: 0.3px;
  }
  .abs { position: absolute; margin: 0; }
  .wave-field { left: 0; top: 690px; width: 848px; height: 320px; }
  .section-heading {
    left: 35px; color: var(--heading-blue); font-weight: 700; font-size: 16px;
    white-space: nowrap; line-height: 1; letter-spacing: 0.3px;
  }
  .bullet-list { list-style: none; padding: 0; line-height: 18.5px; white-space: nowrap; }
  .bullet-list li::before { content: "• "; }
  .bullet-list li.continued::before { content: none; }
  .cert-banner {
    left: 79px; top: 299px; width: 643px; height: 74px; background: var(--banner-grey);
    font-family: "Roboto Condensed", "Arial Narrow", sans-serif; font-weight: 700;
    font-size: 21px; line-height: 25px; color: #2a2a2a; text-align: center; letter-spacing: -0.2px;
    display: flex; align-items: center; justify-content: center;
  }
  .flagship-frame {
    left: 35px; top: 442px; width: 783px; height: 90px; border: 1px solid var(--frame-blue); box-sizing: border-box;
  }
  .flagship-panel {
    left: 45px; top: 452px; width: 763px; height: 72px; background: var(--panel-grey);
    box-sizing: border-box; padding: 9px 30px 0 24px; line-height: 18.5px;
  }
  .body-text { line-height: 18.5px; }
  .tolerance-icon { left: 36px; width: 30px; height: 30px; }
  .tolerance-label { left: 78px; line-height: 1; white-space: nowrap; }
  .coupon-title {
    left: 0; width: 848px; top: 867px; text-align: center; font-weight: 700; font-size: 15.5px; letter-spacing: 0.6px;
  }
  .tip-label {
    left: 606px; top: 905px; width: 170px; height: 29px; border: 1px solid var(--tip-red);
    box-sizing: border-box; text-align: center; line-height: 27px; background: #fff; white-space: nowrap;
  }
  .coupon-photo { top: 940px; height: 135px; }
  .coupon-photo.ground { left: 155px; width: 224px; background: linear-gradient(180deg, #eceef0, #c4c8cb); }
  .coupon-photo.turned { left: 453px; width: 224px; background: linear-gradient(180deg, #c6c9c1, #939889); }
  .caption { width: 320px; text-align: center; top: 1090px; white-space: nowrap; }
</style>
</head>
<body>

<svg class="abs wave-field" viewBox="0 0 848 320" role="img" aria-label="Soft flowing light blue line pattern in the background">
  <defs>
    <linearGradient id="waveFade" x1="0" y1="1" x2="1" y2="0">
      <stop offset="0" stop-color="#d9e8f6" stop-opacity="0.8"/>
      <stop offset="0.5" stop-color="#eef4fb" stop-opacity="0.4"/>
      <stop offset="1" stop-color="#d9e8f6" stop-opacity="0.7"/>
    </linearGradient>
  </defs>
  <path d="M0 300 C220 200 420 170 560 120 C680 80 780 40 848 10 L848 130 C740 160 600 180 480 200 C320 230 150 260 0 320 Z" fill="url(#waveFade)"/>
</svg>

<h2 class="abs section-heading" style="top:55px">Test specimens manufactured by our developed technologies will allow you to:</h2>
<ul class="abs bullet-list" style="left:78px; top:73px">
  <li>Obtain better test results for process qualification</li>
  <li>Improve reduced testing and sampling plan</li>
  <li>Stabilize statistical process control indicators</li>
  <li>Decrease warehouse inventory</li>
  <li>Receive continuous and timely deliveries</li>
</ul>

<h2 class="abs section-heading" style="top:217px">We guarantee delivery of high quality and functional products as a result of:</h2>
<ul class="abs bullet-list" style="left:78px; top:235px">
  <li>Years of experience of manufacturing and testing in the aerospace industry,</li>
  <li class="continued">mainly surface engineering allow us to provide specimens with the highest quality requirements</li>
  <li>ISO 9001:2015 certification for</li>
</ul>

<div class="abs cert-banner">Metalworking difficult-to-machine materials including superalloys<br>and titanium alloys. Design of parts and manufacturing related-tools.</div>

<ul class="abs bullet-list" style="left:78px; top:383px">
  <li>proven machining processes of nickel &amp; cobalt base superalloys, titanium, and hardened steel</li>
  <li>fixed manufacturing processes for specimens preparation</li>
</ul>

<div class="abs flagship-frame"></div>
<p class="abs flagship-panel">Test coupons also called “test buttons” for tensile / bond strength test of coatings are our flagship product. We know how many variables are in testing and we do our best to minimize their influence on the test results.</p>

<p class="abs body-text" style="left:35px; top:547px; width:750px">Thanks to our proprietary manufacturing process we can make test buttons with tight tolerances up to 0.0004 inch or 0.01 mm TIR of:</p>

<svg class="abs tolerance-icon" style="top:598px" viewBox="0 0 30 30">
  <rect x="0.5" y="5" width="28" height="21" fill="none" stroke="var(--icon-orange)"/>
  <path d="M9 11 H22 L19 20 H6 Z" fill="none" stroke="var(--icon-orange)"/>
</svg>
<span class="abs tolerance-label" style="top:604px">flatness of flat surfaces</span>

<svg class="abs tolerance-icon" style="top:635px" viewBox="0 0 30 30">
  <rect x="0.5" y="5" width="28" height="21" fill="none" stroke="var(--icon-orange)"/>
  <path d="M11 21 L14 12 M15 21 L18 12" stroke="var(--icon-orange)"/>
</svg>
<span class="abs tolerance-label" style="top:640px">parallelism of flat surfaces</span>

<svg class="abs tolerance-icon" style="top:671px" viewBox="0 0 30 30">
  <circle cx="15" cy="15" r="14" fill="none" stroke="var(--icon-orange)"/>
  <path d="M0 30 L30 0" stroke="var(--icon-orange)"/>
</svg>
<span class="abs tolerance-label" style="top:678px">outside diameter</span>

<span class="abs tolerance-label" style="left:35px; top:715px">and with:</span>

<svg class="abs tolerance-icon" style="top:740px" viewBox="0 0 30 30">
  <path d="M0 20 L14 30 L30 1" fill="none" stroke="var(--icon-orange)"/>
</svg>
<span class="abs tolerance-label" style="top:752px">similar surface finish as the part</span>

<p class="abs" style="left:40px; top:788px; line-height:1; white-space:nowrap">for the good roughness correlation of the part and the specimen after grit blasting.</p>

<h2 class="abs section-heading" style="top:830px">The results of the fabrication are:</h2>

<p class="abs coupon-title">TENSILE / BOLD STRENGTH OF COATING TEST COUPON / BUTON</p>

<div class="abs coupon-photo ground" role="img" aria-label="Photo of a precisely ground flat test button with a green flatness and parallelism marking"></div>
<div class="abs coupon-photo turned" role="img" aria-label="Photo of a conventionally turned test button with a centre material tip and a red curved-surface marking"></div>

<div class="abs tip-label">additional material tip</div>

<p class="abs caption" style="left:107px">Vermondix fabrication</p>
<p class="abs caption" style="left:411px">Conventional machining by turning</p>

<p class="abs" style="left:36px; top:1141px; line-height:1">Furthermore, our quality inspection staff check each one of them.</p>

</body>
</html>
```